Australian Trucking Company Requires Professional Looking Stationary

We require a professional looking stationary design that incorporates our newly designed logo.

Our business, called "Brell Haulage Contracting", provides contracting work, transport and logistics to business in Western Australia particularly with links to the mining sector.

We are a small business looking to expand and our new logo and our new stationary will help develop our brand image in our market place.

Target Market(s)

Businesses and Corporation with links to the Mining Sector

Industry/Entity Type

Small Business

Requirements
Must have
• The letterhead must have the following details:
The new logo

Text saying: "Brell Holdings Pty Ltd (ACN 582 316 907) ATF The Brell Discretionary Trust T/AS"
"ABN 71 834 209 553"
Address "P.O Box 817 Wattlegrove WA, 6958"
Phone: 08 9352 7140
Email: brellhaul@mailbox-example.com.au

The text on the letterhead should be editable as the details are likely to change in the near future. Provision should be made for a website address all though one isn't available at the moment.

The styling, layout and font text is entirely up to the designer.

```html
<!DOCTYPE html>
<html lang="en">
<head>
<meta charset="utf-8">
<title>Brell Haulage Contracting – Business Card</title>
<link href="https://fonts.googleapis.com/css2?family=Open+Sans:wght@400;700;800&display=swap" rel="stylesheet">
<style>
  :root {
    --stage: #ececec;
    --red-deep: #7e0910;
    --red-mid: #b0121b;
    --red-bright: #d9232c;
    --brand-red: #b3141c;
    --white: #ffffff;
    --band-light: #ffffff;
    --band-shade: #d9d9d9;
    --silver-light: #fafafa;
    --silver-dark: #c9c9c9;
    --rule: rgba(255,255,255,0.55);
    --fine-print: rgba(255,255,255,0.88);
  }
  * { box-sizing: border-box; margin: 0; padding: 0; }
  html, body {
    width: 1200px; height: 426px; overflow: hidden;
    background: var(--stage);
    font-family: "Open Sans", Arial, sans-serif;
  }
  .canvas { position: relative; width: 1200px; height: 426px; }

  .card {
    position: absolute; top: 56px;
    width: 518px; height: 321px;
    border-radius: 16px; overflow: hidden;
  }

  /* Front */
  .card-front {
    left: 68px;
    background: radial-gradient(ellipse 75% 90% at 62% 60%, var(--red-bright) 0%, var(--red-mid) 45%, var(--red-deep) 100%);
    color: var(--white);
  }
  .holder {
    position: absolute; left: 30px; top: 20px;
    font-size: 17px; font-weight: 700;
  }
  .holder .role { font-size: 12px; font-weight: 400; }

  .brand-band {
    position: absolute; left: 60px; right: 0; top: 61px; height: 121px;
    border-radius: 60px 0 0 60px;
    background: linear-gradient(180deg, var(--band-light) 0%, #f1f1f1 60%, var(--band-shade) 100%);
  }
  .brand-name {
    position: absolute; left: 150px; top: 12px;
    color: var(--brand-red);
    font-size: 29px; font-weight: 800; line-height: 32px;
    text-transform: uppercase; letter-spacing: 0.5px;
  }

  .contact {
    position: absolute; right: 30px; top: 192px;
    font-size: 12px; text-align: right; line-height: 22px;
  }
  .contact-line { display: flex; justify-content: flex-end; align-items: center; gap: 5px; }
  .contact-line .gap { width: 8px; }
  .icon { width: 10px; height: 10px; fill: var(--white); }

  .rule {
    position: absolute; left: 30px; right: 30px; top: 244px;
    border-top: 1px solid var(--rule);
  }
  .legal {
    position: absolute; left: 28px; top: 251px;
    font-size: 11px; line-height: 15px; color: var(--fine-print);
  }

  /* Back */
  .card-back {
    left: 617px;
    background: radial-gradient(ellipse 80% 90% at 40% 35%, var(--silver-light) 0%, #eaeaea 55%, var(--silver-dark) 100%);
  }
  .back-brand {
    position: absolute; left: 0; right: 0; top: 50%; transform: translateY(-50%);
    text-align: center;
    color: var(--brand-red);
    font-size: 32px; font-weight: 800; line-height: 36px;
    text-transform: uppercase; letter-spacing: 0.5px;
  }
</style>
</head>
<body>
<main class="canvas">

  <section class="card card-front" aria-label="Business card front">
    <p class="holder">Persons name, <span class="role">Manager</span></p>

    <div class="brand-band">
      <p class="brand-name">Brell<br>Haulage<br>Contracting</p>
    </div>

    <div class="contact">
      <p class="contact-line">
        <svg class="icon" viewBox="0 0 10 10" aria-hidden="true"><path d="M5 0.5 L10 5 H8.5 V9.5 H6 V6.5 H4 V9.5 H1.5 V5 H0 Z"/></svg>
        P.O Box 817 Wattlegrove WA, 6958
      </p>
      <p class="contact-line">
        <svg class="icon" viewBox="0 0 10 10" aria-hidden="true"><path d="M2.2 0.6 L3.8 2.8 L2.9 3.9 C3.5 5.2 4.8 6.5 6.1 7.1 L7.2 6.2 L9.4 7.8 L8.5 9.4 C4.5 9.2 0.8 5.5 0.6 1.5 Z"/></svg>
        08 9352 7140
        <span class="gap"></span>
        <svg class="icon" viewBox="0 0 10 10" aria-hidden="true"><path d="M0.5 2 H9.5 V8.5 H0.5 Z M1.3 2.8 V7.7 H8.7 V2.8 L5 5.6 Z" fill-rule="evenodd"/></svg>
        brellhaul@mailbox-example.com.au
      </p>
    </div>

    <div class="rule"></div>

    <p class="legal">
      Brell Holdings Pty Ltd&nbsp; (ACN 582 316 907) ATF The Brell Discretionary Trust T/AS<br>
      ABN 71 834 209 553
    </p>
  </section>

  <section class="card card-back" aria-label="Business card back">
    <p class="back-brand">Brell<br>Haulage<br>Contracting</p>
  </section>

</main>
</body>
</html>
```